Casino with the 'highest winning percentage' needs a stationery design

This is for a casino in Colombo, Sri Lanka and we need a stationery design for business card, letter head and envelope.

Should be very professional, simple and elegant without fancy fonts

Reason: Not fully satisfied with the designs. Need more designs.

Business

• 1. card deck symbol 'CLUBS' in red, or black

2. name in BLOCK CAPITAL LETTERS

3. Preferred font colours are black, white or red

4. Prefer 'professional /elegant' fonts
• SHOULD NOT HAVE ANY OTHER SYMBOL EXCEPT 'CLUBS'

DO NOT PREFER ITALIC FONTS

```html
<!DOCTYPE html>
<html lang="en">
<head>
<meta charset="utf-8">
<title>Corvin's Entertainment – Business Card</title>
<link href="https://fonts.googleapis.com/css2?family=Noto+Serif:wght@400;700&display=swap" rel="stylesheet">
<style>
  :root {
    --red: #d62c40;
    --black: #1f1e1f;
    --ink: #222222;
    --white: #ffffff;
    --stage: #e9e6e2;
    --rule: #cfcfcf;
  }
  * { box-sizing: border-box; margin: 0; padding: 0; }
  html, body { width: 1200px; height: 1057px; overflow: hidden; }
  body {
    background: var(--stage);
    font-family: "Noto Serif", Georgia, serif;
    color: var(--ink);
    position: relative;
  }
  .card {
    position: absolute;
    left: 180px;
    width: 840px;
    height: 480px;
    overflow: hidden;
    box-shadow: 0 6px 18px rgba(0,0,0,.18);
  }
  .card--front { top: 32px; background: var(--white); }
  .card--back { top: 545px; background: var(--black); }

  .wave { position: absolute; left: 0; top: 0; width: 840px; height: 480px; }

  .brand-mark {
    position: absolute;
    width: 130px; height: 130px;
    border-radius: 50%;
    background: var(--red);
  }
  .card--front .brand-mark { left: 90px; top: 135px; }
  .card--back .brand-mark { left: 120px; top: 150px; }

  .brand-name {
    position: absolute;
    font-weight: 700;
    font-size: 44px;
    line-height: 1.1;
    letter-spacing: 1px;
    text-transform: uppercase;
  }
  .card--front .brand-name { left: 330px; top: 36px; color: var(--ink); }
  .card--back .brand-name { left: 300px; top: 140px; color: var(--white); }

  .company {
    position: absolute;
    right: 420px;
    top: 190px;
    text-align: right;
    font-size: 15px;
    line-height: 1.35;
  }
  .company__name {
    color: var(--red);
    font-weight: 700;
    font-size: 20px;
    text-transform: uppercase;
    margin-bottom: 4px;
  }
  .divider {
    position: absolute;
    left: 445px; top: 180px;
    width: 1px; height: 110px;
    background: var(--rule);
  }
  .contacts {
    position: absolute;
    left: 465px; top: 180px;
    list-style: none;
    font-size: 15px;
    line-height: 1.55;
  }
  .contacts li { display: flex; align-items: center; gap: 9px; }
  .contacts svg { width: 14px; height: 14px; fill: var(--red); flex: none; }

  .website {
    position: absolute;
    left: 34px; top: 436px;
    color: var(--white);
    font-size: 14px;
    letter-spacing: 4px;
  }

  .tagline {
    position: absolute;
    left: 0; right: 0; top: 350px;
    text-align: center;
    color: var(--white);
    font-weight: 700;
    font-size: 22px;
    letter-spacing: 3px;
  }
</style>
</head>
<body>

<section class="card card--front" aria-label="Business card front">
  <svg class="wave" viewBox="0 0 840 480" aria-hidden="true">
    <path d="M0,372 C220,362 420,334 560,314 C680,299 780,290 840,284" fill="none" stroke="var(--red)" stroke-width="3"/>
    <path d="M0,382 C220,372 420,344 560,324 C680,309 780,300 840,294" fill="none" stroke="var(--black)" stroke-width="5"/>
    <path d="M0,392 C220,382 420,354 560,334 C680,319 780,310 840,304 L840,326 C760,338 660,364 520,402 C380,442 270,470 210,480 L0,480 Z" fill="var(--red)"/>
  </svg>

  <div class="brand-mark" aria-hidden="true"></div>
  <h1 class="brand-name">Corvin's<br>Entertainment</h1>

  <div class="company">
    <p class="company__name">Corvin's Limited</p>
    <p>27, Palm Grove Mawatha</p>
    <p>Colombo 01000</p>
    <p>Sri Lanka</p>
  </div>

  <div class="divider"></div>

  <ul class="contacts">
    <li><svg viewBox="0 0 14 14"><path d="M3 1l2.5 3-1.5 1.5c.8 1.8 2 3 3.8 3.8L9.3 7.8 12.5 10.3 11 13C5.5 12.5 1.5 8.5 1 3z"/></svg>+94 11 2456780</li>
    <li><svg viewBox="0 0 14 14"><path d="M4 0h6a1 1 0 0 1 1 1v12a1 1 0 0 1-1 1H4a1 1 0 0 1-1-1V1a1 1 0 0 1 1-1zm1 2v8h4V2z"/></svg>+94 77 0000000</li>
    <li><svg viewBox="0 0 14 14"><path d="M1 6h12v7H1zM3 1h8v4H3z"/></svg>+94 11 0000000</li>
    <li><svg viewBox="0 0 14 14"><path d="M0 3h14v8H0zm1 1l6 4 6-4v-.2H1z"/></svg>info@corvinscolombo.com</li>
  </ul>

  <p class="website">www.corvinscolombo.com</p>
</section>

<section class="card card--back" aria-label="Business card back">
  <div class="brand-mark" aria-hidden="true"></div>
  <h2 class="brand-name">Corvin's<br>Entertainment</h2>
  <p class="tagline">Highest Winning Percentage In The World</p>
</section>

</body>
</html>
```